Velmora Systems Website

Website design for our company: Velmora Systems.
The website should look fresh and IT focused. Please have a look at http://www.velmorasystems.example.au/ for our current design. We want something fresh and new, professional looking, in WordPress so we can easily make changes.

It Company

```html
<!DOCTYPE html>
<html lang="en">
<head>
<meta charset="utf-8">
<title>Velmora Systems</title>
<link href="https://fonts.googleapis.com/css2?family=Open+Sans:ital,wght@0,300;0,400;0,600;0,700;1,800&display=swap" rel="stylesheet">
<style>
:root{
  --green:#1aa84f;
  --green-bright:#27b34a;
  --green-soft:#8cc63f;
  --nav:#3b3f4c;
  --ink:#1f2a33;
  --muted:#a9a9a9;
  --light:#f1f1f1;
  --footer:#2b2b2b;
  --footer-text:#9a9a9a;
  --white:#ffffff;
}
*{box-sizing:border-box;margin:0;padding:0}
html,body{width:769px;height:1200px;overflow:hidden;background:var(--white)}
body{font-family:"Open Sans",Arial,sans-serif;color:var(--ink);position:relative}
.page{position:relative;width:769px;height:1200px}

/* header */
.site-header{position:absolute;top:0;left:0;width:769px;height:69px}
.brand{position:absolute;left:83px;top:10px;display:flex;align-items:center;gap:8px}
.brand-mark{width:26px;height:26px;background:var(--green)}
.brand-name{font-size:20px;font-weight:600;color:var(--green)}
.search{position:absolute;left:547px;top:9px;width:140px;height:21px;background:var(--green);display:flex;align-items:center;justify-content:space-between;padding:0 7px;color:var(--white);font-size:9px}
.follow{position:absolute;left:536px;top:40px;display:flex;align-items:center;gap:6px;font-size:12px;font-weight:700;color:var(--green);letter-spacing:.5px}
.follow .dot{width:19px;height:19px;border:1.5px solid #222;border-radius:50%}

.main-nav{position:absolute;top:69px;left:83px;width:604px;height:33px;background:var(--nav);display:flex}
.main-nav a{color:var(--white);text-decoration:none;font-size:9px;font-weight:600;padding:0 10px;line-height:33px}
.main-nav a.active{background:var(--green)}

/* hero */
.hero{position:absolute;top:102px;left:21px;width:727px;height:240px;
  background:radial-gradient(ellipse at 45% 35%,#5f88a3 0%,#2e5a74 40%,#132a3a 100%)}
.hero-art{position:absolute;left:110px;top:6px;width:500px;height:200px;
  background:linear-gradient(100deg,#c9d1d9 0%,#7a4fb0 45%,#d9d9e0 65%,#1c1c22 85%);opacity:.55;border-radius:4px}
.hero-title{position:absolute;top:208px;left:0;width:100%;text-align:center;color:var(--white);font-size:24px;font-weight:800;font-style:italic;letter-spacing:.5px}
.hero-rule{position:absolute;top:203px;left:0;width:100%;height:1px;background:rgba(255,255,255,.25)}

/* services */
.services{position:absolute;top:342px;left:21px;width:727px;height:188px;background:var(--light)}
.service-col{position:absolute;top:28px;width:180px}
.service-head{display:flex;gap:12px;align-items:flex-start;margin-bottom:18px}
.num{width:27px;height:27px;background:#3d434c;color:var(--white);font-size:11px;display:flex;align-items:center;justify-content:center}
.service-title{font-size:15px;line-height:16px;color:var(--ink);text-transform:uppercase}
.service-title span{display:block;color:var(--green-soft);font-weight:300}
.service-list{list-style:none}
.service-list li{font-size:8.5px;color:var(--muted);height:23px;display:flex;align-items:center;gap:12px;white-space:nowrap}
.service-list li::before{content:"›";color:#333;font-size:14px;font-weight:700}

/* feature band */
.features{position:absolute;top:530px;left:21px;width:727px;height:224px;
  background:linear-gradient(180deg,#3d4246 0%,#55595b 45%,#6d6a66 100%)}
.features-photo{position:absolute;inset:0;background:radial-gradient(ellipse at 82% 30%,rgba(110,85,70,.55),rgba(0,0,0,0) 45%)}
.feature{position:absolute;top:32px;width:190px;text-align:center;color:var(--white)}
.feature-icon{width:70px;height:70px;border-radius:50%;background:var(--green);margin:0 auto 12px;display:flex;align-items:center;justify-content:center}
.feature h3{font-size:14px;font-weight:400;margin-bottom:4px}
.feature p{font-size:8.5px;font-weight:600;line-height:13px}

/* info columns */
.info-col{position:absolute;top:772px;width:170px}
.info-col h2{font-size:16px;font-weight:600;line-height:15px;margin-bottom:9px}
.info-col p{font-size:8px;color:var(--muted);line-height:12px;margin-bottom:8px}
.info-list{list-style:none}
.info-list li{font-size:8px;color:var(--green);height:23px;border-bottom:1px solid #eee;display:flex;align-items:center;gap:10px;padding-left:6px;white-space:nowrap}
.info-list li::before{content:"";width:5px;height:5px;border-radius:50%;background:#111;flex:none}
.btn-more{display:inline-block;margin-top:12px;background:#333;color:var(--white);font-size:9px;font-weight:700;padding:5px 15px}

/* footer */
.site-footer{position:absolute;top:1010px;left:21px;width:727px;height:162px;background:var(--footer)}
.foot-col{position:absolute;top:22px}
.foot-col h4{font-size:10px;font-weight:600;color:var(--white);margin-bottom:9px}
.foot-col ul{list-style:none}
.foot-col li{font-size:7.5px;color:var(--footer-text);line-height:15px}
.foot-col li.current{color:var(--green-bright)}
.contact-row{display:flex;align-items:center;gap:6px;font-size:7.5px;color:var(--footer-text);margin-bottom:8px;white-space:nowrap}
.contact-row strong{color:var(--white);font-size:10px;font-weight:400}
.contact-row .mail{color:var(--green-bright)}
.foot-social{display:flex;gap:8px;margin-top:2px}
.foot-social span{width:10px;height:10px;background:#777;border-radius:2px}
.remote-label{font-size:7.5px;color:var(--footer-text);margin-bottom:8px}
.remote-input{width:152px;height:20px;background:var(--white);font-size:7.5px;color:#aaa;padding:5px 6px}
.remote-btn{width:152px;height:21px;margin-top:5px;background:var(--green-bright);color:var(--white);font-size:9px;font-weight:600;text-align:center;line-height:21px}
.bottom-bar{position:absolute;top:1172px;left:21px;width:727px;height:27px;background:var(--green);color:var(--white);font-size:8px;text-align:center;line-height:27px}
</style>
</head>
<body>
<div class="page">

  <header class="site-header">
    <div class="brand"><span class="brand-mark"></span><span class="brand-name">Velmora Systems</span></div>
    <div class="search"><span>Search</span>
      <svg width="11" height="11" viewBox="0 0 12 12"><circle cx="5" cy="5" r="3.6" fill="none" stroke="#fff" stroke-width="1.6"/><line x1="7.6" y1="7.6" x2="11" y2="11" stroke="#fff" stroke-width="1.8"/></svg>
    </div>
    <div class="follow">FOLLOW US <span class="dot"></span><span class="dot"></span><span class="dot"></span></div>
  </header>

  <nav class="main-nav">
    <a class="active">HOME</a><a>SUPPLIERS</a><a>SERVICES</a><a>SUPPORTS</a><a>TESTIMONIALS</a><a>CONTACT US</a><a>ABOUT US</a>
  </nav>

  <section class="hero">
    <div class="hero-art" role="img" aria-label="Laptop, desktop monitor and tablet displayed together"></div>
    <div class="hero-rule"></div>
    <h1 class="hero-title">BEST COMPUTER REPAIR</h1>
  </section>

  <section class="services">
    <div class="service-col" style="left:79px">
      <div class="service-head"><div class="num">01</div><div class="service-title">Home<span>Services</span></div></div>
      <ul class="service-list"><li>Same Day In-Home Support</li><li>Certified Technicians</li><li>Virus &amp; Spyware Removal</li><li>Wireless Networking</li></ul>
    </div>
    <div class="service-col" style="left:273px">
      <div class="service-head"><div class="num">02</div><div class="service-title">Business<span>Services</span></div></div>
      <ul class="service-list"><li>On-site Engineers</li><li>AD, Mail Server, SQL</li><li>Vendor Certified</li><li>Maintenance Contracts</li></ul>
    </div>
    <div class="service-col" style="left:467px">
      <div class="service-head"><div class="num">03</div><div class="service-title">Nationwide<span>IT Services</span></div></div>
      <ul class="service-list"><li>Nationwide IT Workforce</li><li>OEM Hardware Installations</li><li>IT Project Management</li><li>Staff Augmentation</li></ul>
    </div>
  </section>

  <section class="features">
    <div class="features-photo" role="img" aria-label="Person working on a laptop against a cloudy sky"></div>
    <div class="feature" style="left:62px">
      <div class="feature-icon"><svg width="24" height="22" viewBox="0 0 24 22"><rect x="1" y="1" width="22" height="14" rx="1" fill="none" stroke="#fff" stroke-width="2.2"/><rect x="9" y="16" width="6" height="3" fill="#fff"/><rect x="6" y="19" width="12" height="2" fill="#fff"/></svg></div>
      <h3>Computer Repair</h3>
      <p>Lorem ipsum dolor sit amet, consectetuer adipiscing elit, sed diam nonummy nibh euismod tincidunt ut laoreet dolore magna aliquam erat volutpat.</p>
    </div>
    <div class="feature" style="left:268px">
      <div class="feature-icon"><svg width="22" height="22" viewBox="0 0 22 22"><circle cx="11" cy="11" r="10" fill="#fff"/><path d="M6 6c3 1 4 3 3 5s1 3 3 4M14 4c-1 2 1 3 3 3" fill="none" stroke="#1aa84f" stroke-width="2"/></svg></div>
      <h3>Internet Services</h3>
      <p>Lorem ipsum dolor sit amet, consectetuer adipiscing elit, sed diam nonummy nibh euismod tincidunt ut laoreet dolore magna aliquam erat volutpat.</p>
    </div>
    <div class="feature" style="left:475px">
      <div class="feature-icon"><svg width="14" height="24" viewBox="0 0 14 24"><rect x="1" y="1" width="12" height="22" rx="2" fill="none" stroke="#fff" stroke-width="2"/><circle cx="7" cy="19" r="1.3" fill="#fff"/></svg></div>
      <h3>Phone Repair</h3>
      <p>Lorem ipsum dolor sit amet, consectetuer adipiscing elit, sed diam nonummy nibh euismod tincidunt ut laoreet dolore magna aliquam erat volutpat.</p>
    </div>
  </section>

  <section class="info">
    <div class="info-col" style="left:82px">
      <h2>Home Computer Services</h2>
      <p>Lorem ipsum dolor sit amet, consectetuer adipiscing elit, sed diam nonummy nibh euismod tincidunt ut laoreet dolore magna aliquam erat volutpat.</p>
      <ul class="info-list"><li>Lorem ipsum dolor sit amet conse</li><li>Ctetur adipiscing elit, sed do eiusmod</li><li>Tempor incididunt ut labore et</li><li>Dolore magna aliquaenim ad minim</li></ul>
      <span class="btn-more">Read more</span>
    </div>
    <div class="info-col" style="left:294px">
      <h2>Home Computer Services</h2>
      <p>Lorem ipsum dolor sit amet, consectetuer adipiscing elit, sed diam nonummy nibh euismod tincidunt ut laoreet dolore magna aliquam erat volutpat.</p>
      <ul class="info-list"><li>Lorem ipsum dolor sit amet conse</li><li>Ctetur adipiscing elit, sed do eiusmod</li><li>Tempor incididunt ut labore et</li><li>Dolore magna aliquaenim ad minim</li></ul>
      <span class="btn-more">Read more</span>
    </div>
    <div class="info-col" style="left:505px">
      <h2>Home Computer Services</h2>
      <p>Lorem ipsum dolor sit amet, consectetuer adipiscing elit, sed diam nonummy nibh euismod tincidunt ut laoreet dolore magna aliquam erat volutpat.</p>
      <ul class="info-list"><li>Lorem ipsum dolor sit amet conse</li><li>Ctetur adipiscing elit, sed do eiusmod</li><li>Tempor incididunt ut labore et</li><li>Dolore magna aliquaenim ad minim</li></ul>
      <span class="btn-more">Read more</span>
    </div>
  </section>

  <footer class="site-footer">
    <div class="foot-col" style="left:61px">
      <h4>Navigation</h4>
      <ul><li class="current">Home</li><li>About</li><li>Services</li><li>News</li><li>Contacts</li></ul>
    </div>
    <div class="foot-col" style="left:155px">
      <h4>Categories</h4>
      <ul><li>Same Day In-Home Support</li><li>Certified Technicians</li><li>Virus &amp; Spyware Removal</li><li>Wireless Networking</li><li>On-site Engineers</li><li>AD, Mail Server, SQL</li></ul>
    </div>
    <div class="foot-col" style="left:294px">
      <h4>Contacts</h4>
      <div class="contact-row"><svg width="9" height="11" viewBox="0 0 9 11"><path d="M4.5 0a4 4 0 0 1 4 4c0 3-4 7-4 7S.5 7 .5 4a4 4 0 0 1 4-4z" fill="#27b34a"/><circle cx="4.5" cy="4" r="1.5" fill="#2b2b2b"/></svg>218 Harbour Lane Kestrel Bay 5099 Australia</div>
      <div class="contact-row"><svg width="11" height="11" viewBox="0 0 11 11"><path d="M2 0l2 3-1.2 1.3a6 6 0 0 0 3.9 3.9L8 7l3 2-1.5 2C5 11 0 6 0 1.5z" fill="#27b34a"/></svg>Call us: <strong>0855501847</strong></div>
      <div class="contact-row"><svg width="13" height="10" viewBox="0 0 13 10"><rect x=".7" y=".7" width="11.6" height="8.6" fill="none" stroke="#27b34a" stroke-width="1.3"/><path d="M1 1l5.5 4.5L12 1" fill="none" stroke="#27b34a" stroke-width="1.3"/></svg><span class="mail">hello@velmorasystems.example</span></div>
      <div class="foot-social"><span></span><span></span><span></span></div>
    </div>
    <div class="foot-col" style="left:514px">
      <h4>Remote Support</h4>
      <div class="remote-label">Enter your 6-digit code</div>
      <div class="remote-input">Enter your 6-digit code</div>
      <div class="remote-btn">Connect Now</div>
    </div>
  </footer>
  <div class="bottom-bar">© 2014 Velmora Systems. All Rights Reserved. Designed &amp; Developed by Northgate Studio</div>

</div>
</body>
</html>
```